Carwash Signage

We own and operate a 25m tunnel car wash in the uk. We are looking to upgrade our signage to include the following:-

Wash selection Board Size-1300x1300mm
Conditions 1300x1300mm
Instructions 1300x1300mm
Banner 2600x600mm
Stamp card flyer a5 double sided - 9 squares for stamping 3rd square needs to say free air freshener 9th square needs to say free vip car wash.

I have attached some notes for the details that are required to be included.

We are looking for a modern smart look more European car wash style than American car wash style. It should be bold and clear. with yellow/orange & blue/green,grey colours

The final design must be in a industry standard printable format.

UPDATED BRIEF AS DISCUSSED: We require design for 2 x window decals, flag design and 50% off voucher. Attached are rough layout drawings of what they should look like - we expect the designs to be in keeping with the previous designs colours, etc that have been carried out. We Look forward to hearing from you.

Target Market(s)

local car owners within a 15-20 mile radius

Colors
0054AA
0677BA
7BADD7
CADEEF
E8F1F8
0094D4
00A9DD
6FCCEA
C7EBF8
E9F6FB
00AB8E
00BBA5
67D7C9
C6EFE9
E9F9F6

Requirements
Must have
• must be sharp and modern European look

```html
<!DOCTYPE html>
<html lang="en">
<head>
<meta charset="utf-8">
<title>Harbourline Car Wash – Banner</title>
<link rel="stylesheet" href="https://fonts.googleapis.com/css2?family=Krona+One&family=Great+Vibes&family=Michroma&display=swap">
<style>
  :root{
    --navy:#1f2a7c;
    --royal:#0054aa;
    --blue:#0677ba;
    --sky:#7badd7;
    --ice:#e8f1f8;
    --pale:#c7ebf8;
    --ink:#111318;
    --white:#ffffff;
    --yellow:#ffd21f;
    --page:#f2f4f7;
  }
  *{box-sizing:border-box;margin:0;padding:0}
  html,body{width:1200px;height:1011px;overflow:hidden;background:var(--page)}
  .banner{
    position:absolute;left:0;top:367px;width:1200px;height:277px;
    background:linear-gradient(180deg,#f4f8fb 0%,var(--ice) 100%);
    overflow:hidden;font-family:"Krona One",sans-serif;
  }
  .photo-foam-car{
    position:absolute;left:0;top:0;width:285px;height:225px;
    background:linear-gradient(90deg,#4f8fd0 0%,#7badd7 45%,#c7ebf8 80%,rgba(232,241,248,0) 100%);
  }
  .photo-washer{
    position:absolute;left:745px;top:86px;width:320px;height:139px;
    background:linear-gradient(90deg,rgba(232,241,248,0) 0%,#5d6b7c 18%,#1c2330 55%,#4a5a6e 85%,rgba(232,241,248,0) 100%);
  }
  .attended{
    position:absolute;left:0;top:30px;width:184px;height:41px;
    background:var(--navy);border:2px solid var(--white);border-left:none;
    border-radius:0 20px 20px 0;color:var(--white);
    font-size:17px;letter-spacing:.5px;display:flex;align-items:center;padding-left:18px;
  }
  .title-car{
    position:absolute;left:282px;top:18px;font-family:"Great Vibes",cursive;
    font-size:118px;line-height:1;color:var(--ink);
  }
  .title-wash{
    position:absolute;left:290px;top:108px;font-size:108px;line-height:1;
    transform:skewX(-14deg);letter-spacing:-4px;
    background:linear-gradient(180deg,#3f7fd6 0%,var(--royal) 55%,var(--navy) 100%);
    -webkit-background-clip:text;background-clip:text;color:transparent;
    -webkit-text-stroke:1px var(--navy);
  }
  .panel{position:absolute;left:0;top:0;width:1200px;height:277px}
  .brand{position:absolute;left:756px;top:16px;width:310px;height:62px}
  .brand-tag{
    position:absolute;right:0;top:0;font-size:14px;letter-spacing:3px;color:var(--ink);
  }
  .brand-name{
    position:absolute;left:0;top:26px;display:flex;align-items:center;gap:8px;
    font-size:28px;color:var(--navy);
  }
  .brand-dot{width:26px;height:26px;border-radius:50%;background:var(--navy)}
  .open{
    position:absolute;left:1030px;top:102px;width:152px;height:37px;
    background:var(--ink);border:2px solid var(--white);border-radius:10px;
    transform:skewX(-16deg);color:var(--white);
    display:flex;align-items:center;justify-content:center;
  }
  .open span{font-size:19px;transform:skewX(6deg)}
  .hours{
    position:absolute;left:1028px;top:168px;width:150px;text-align:center;
    font-family:"Krona One",sans-serif;
  }
  .hours .day{color:var(--white);font-size:15px;line-height:18px}
  .hours .time{color:var(--yellow);font-size:16px;line-height:22px}
  .hours hr{border:none;border-top:1px solid rgba(255,255,255,.8);margin:5px 0 5px}
  .payments{
    position:absolute;left:0;top:225px;width:975px;height:52px;
    display:flex;align-items:center;padding-left:20px;color:var(--white);
  }
  .payments-text{font-size:19px;letter-spacing:6px;white-space:nowrap}
  .cards{display:flex;gap:7px;margin-left:58px}
  .card{width:31px;height:20px;border-radius:3px}
  .card-a{background:#2b2b2b;border:1px solid #555}
  .card-b{background:#1f5fbf}
  .card-c{background:#e8502a}
  .card-d{background:#3b3f7a}
</style>
</head>
<body>
  <section class="banner">
    <div class="photo-foam-car" role="img" aria-label="Photo of a foam-covered car being washed"></div>

    <svg class="panel" viewBox="0 0 1200 277" aria-hidden="true">
      <polygon points="0,225 990,225 968,277 0,277" fill="#111318"/>
      <polygon points="1062,0 1083,0 966,277 944,277" fill="#ffffff"/>
      <polygon points="1083,0 1200,0 1200,277 966,277" fill="#0054aa"/>
      <polygon points="1110,0 1200,0 1200,277 1000,277" fill="#1f2a7c" opacity=".55"/>
    </svg>

    <div class="photo-washer" role="img" aria-label="Photo of workers pressure washing a dark SUV"></div>

    <div class="attended">ATTENDED</div>
    <div class="title-car">Car</div>
    <div class="title-wash">WASH</div>

    <div class="brand">
      <div class="brand-tag">CAR WASH</div>
      <div class="brand-name"><span class="brand-dot"></span>HARBOURLINE</div>
    </div>

    <div class="open"><span>OPEN</span></div>
    <div class="hours">
      <div class="day">MON-SAT</div>
      <div class="time">8:00 - 18:00</div>
      <hr>
      <div class="day">SUN</div>
      <div class="time">9:00 - 18:00</div>
    </div>

    <div class="payments">
      <span class="payments-text">CASH + CARD PAYMENTS ACCEPTED</span>
      <div class="cards">
        <span class="card card-a"></span>
        <span class="card card-b"></span>
        <span class="card card-c"></span>
        <span class="card card-d"></span>
      </div>
    </div>
  </section>
</body>
</html>
```